Brightway Haus Inc. Business Card Design

Brightway Haus Inc. is in search of a great clean design for our business cards!

Looking to incorporate our full logo and watermark on side one (however, I am open to having the text and watermark separated within the design.)

On side two, I am looking to have contact information (Name, Position, Phone #, Email, Website (www.thebrightwayhaus.ca). Can have the logo and/or watermark as part of the design if applicable.

Please add tagline "Where Shine Counts" on either side 1 or 2. This tagline can be in a sans serif, serif or cursive font as long as it compliments overall design. Capitalization can be title or sentence case depending on how it fits within the design.

Get creative!! Looking for a clean, crisp, premium design! Looking for a glossy card finish with spot UV features when printed. Cards will also be printed with rounded corners. Standard dimensions (3.5 x 2).

Target Market(s)

B2B - primary clients are business owners or property management corporations. (residential jobs are few and far between)

Industry/Entity Type

Business

Contact Information for Business Card

- clean, crisp design
- double sided
- spot UV accents and glossy finish upon printing
- standard business card size (3.5 x 2) with rounded corners
- please see project description for requirements per side

Font styles to use
Sans Serif

Requirements
Must have
• - adequate bleeds with print ready files
• - cohesive design elements between side 1 & 2
• - spot UV elements (can be on both sides or just one, use your discretion)
• - colour pallet should match the logo file provided
• - incorporate tagline "where shine counts" (this tagline can be in a serif or sans serif font as long as it is complimentary to the overall design.
Nice to have
• - Premium elements with a clean design
Should not have
• - Please omit cartoon or whimsical like designs, think premium.
• - Colours should not stray from the pallet of the provided logo.

```html
<!DOCTYPE html>
<html lang="en">
<head>
<meta charset="utf-8">
<title>Brightway Haus Inc. Business Card</title>
<link href="https://fonts.googleapis.com/css2?family=Open+Sans:wght@400;600;700&display=swap" rel="stylesheet">
<style>
  :root {
    --backdrop: #2a2a2b;
    --paper: #ffffff;
    --teal: #17b5bd;
    --navy: #1b2553;
    --ink: #4a4a4a;
    --rule: #3c3c3c;
    --white: #ffffff;
  }
  * { margin: 0; padding: 0; box-sizing: border-box; }
  html, body {
    width: 1200px; height: 960px; overflow: hidden;
    background: var(--backdrop);
    font-family: "Open Sans", Arial, sans-serif;
  }
  .canvas { position: relative; width: 1200px; height: 960px; }

  .card {
    position: absolute;
    width: 600px; height: 343px;
    border-radius: 18px;
    overflow: hidden;
  }
  .card--front { left: 314px; top: 113px; background: var(--paper); }
  .card--back { left: 311px; top: 472px; background: var(--navy); }

  .brand-name {
    position: absolute;
    font-weight: 700;
    letter-spacing: -0.5px;
    white-space: nowrap;
  }
  .card--front .brand-name {
    right: 32px; top: 58px;
    font-size: 24px; color: var(--navy);
  }
  .card--back .brand-name {
    left: 0; right: 0; top: 144px;
    text-align: center;
    font-size: 36px; color: var(--white);
  }

  .holder { position: absolute; left: 25px; top: 192px; }
  .holder__name { font-size: 15px; font-weight: 700; color: var(--teal); line-height: 20px; }
  .holder__title { font-size: 16px; color: var(--navy); line-height: 22px; }

  .divider {
    position: absolute; left: 29px; top: 243px;
    width: 536px; height: 1px; background: var(--rule);
  }

  .contact-list { position: absolute; left: 27px; top: 255px; list-style: none; }
  .contact-list li {
    display: flex; align-items: center; gap: 8px;
    font-size: 14px; color: var(--ink); line-height: 19px;
  }
  .contact-list svg { width: 14px; height: 14px; fill: var(--teal); flex: none; }

  .address {
    position: absolute; right: 31px; top: 261px;
    text-align: right; font-size: 14px; color: var(--ink); line-height: 18.5px;
  }

  .accent-band { position: absolute; left: 0; bottom: 0; width: 600px; height: 12px; }

  .tagline {
    position: absolute; left: 0; right: 0; top: 276px;
    display: flex; align-items: center; justify-content: center; gap: 2px;
    color: var(--white); font-size: 17px; font-weight: 600;
  }
  .tagline__line { width: 115px; height: 1px; }
  .tagline__line--left { background: linear-gradient(to right, rgba(255,255,255,0), rgba(255,255,255,0.9)); }
  .tagline__line--right { background: linear-gradient(to left, rgba(255,255,255,0), rgba(255,255,255,0.9)); }
</style>
</head>
<body>
<main class="canvas">

  <section class="card card--front" aria-label="Business card front">
    <div class="brand-name">BRIGHTWAY HAUS INC.</div>

    <div class="holder">
      <p class="holder__name">DANA WHITFIELD</p>
      <p class="holder__title">CEO/FOUNDER</p>
    </div>

    <div class="divider"></div>

    <ul class="contact-list">
      <li>
        <svg viewBox="0 0 16 16" aria-hidden="true"><path d="M2 6c0-2 2-3 6-3s6 1 6 3v1h-3V5.5H5V7H2zM4 8h8l1 5H3z M8 9.5a1.5 1.5 0 1 0 0 3 1.5 1.5 0 0 0 0-3z"/></svg>
        604 555 0182
      </li>
      <li>
        <svg viewBox="0 0 16 16" aria-hidden="true"><path d="M4.5 1h7v14h-7zM6 2.8v9h4v-9zM7.3 13h1.4v1H7.3z"/></svg>
        604 555 0247
      </li>
      <li>
        <svg viewBox="0 0 16 16" aria-hidden="true"><path d="M2 4.5h12v1L8 9 2 5.5zM2 7l6 3.5L14 7v5H2z"/></svg>
        hello@brightwayhaus.ca
      </li>
    </ul>

    <address class="address" style="font-style:normal">
      1420 Harbour Crescent<br>
      Vancouver, BC V6B 0A1<br>
      www.thebrightwayhaus.ca
    </address>

    <svg class="accent-band" viewBox="0 0 600 12" preserveAspectRatio="none" aria-hidden="true">
      <polygon points="0,0 385,0 381,12 0,12" fill="var(--teal)"/>
      <polygon points="389,0 600,0 600,12 385,12" fill="var(--navy)"/>
    </svg>
  </section>

  <section class="card card--back" aria-label="Business card back">
    <div class="brand-name">BRIGHTWAY HAUS INC.</div>
    <p class="tagline">
      <span class="tagline__line tagline__line--left"></span>
      Where Shine Counts
      <span class="tagline__line tagline__line--right"></span>
    </p>
  </section>

</main>
</body>
</html>
```